Vindgerdi - Start-up company selling electricity

Hello let me tell you about Vindgerdi.

Vindgerdi is start-up company selling electricity in Iceland. The operations of the company consist of making power usage forecasts for our customers, purchasing the electricity wholesale from the energy producers, and selling the electricity to the consumer. We are focused on tech by using optimization and machine learning to minimize electricity prices to our customers. Our marketing strategy is to portray a tech company mindset and to show dedication to driving down the electricity price on the market.

We need your help to make our website pop. Possible concepts to work with are as follows:

- Iceland the land of ice and fire
- Green energy
- Innovation
- Tech and data science

Link to our website: https://prufa.vindgerdi-example.is/
We are open to ideas.
Thank you!

Target Market(s)

Electricity consumers both homes and companies.

Number of Pages Required

1 page

Font styles to use
Serif
Sans Serif

```html
<!DOCTYPE html>
<html lang="is">
<head>
<meta charset="utf-8">
<title>Vindgerdi – Sama rafmagn, bara ódýrara</title>
<link rel="stylesheet" href="https://fonts.googleapis.com/css2?family=Jost:wght@400;600&family=Poppins:wght@400;500&family=Fira+Sans:wght@400;500;600&display=swap">
<style>
  :root {
    --backdrop: #8fb9e0;
    --surface: #ffffff;
    --navy: #1e2553;
    --ink: #333845;
    --muted: #5a5e6b;
    --coral: #df636b;
    --sky: #568bc6;
    --alert: #dc3f4b;
    --line: #cfd5e8;
    --green: #1ea47b;
  }
  * { margin: 0; padding: 0; box-sizing: border-box; }
  html, body { width: 1200px; height: 849px; overflow: hidden; }
  body { background: var(--backdrop); position: relative; font-family: "Jost", sans-serif; color: var(--navy); }

  .page {
    position: absolute; left: 106px; top: 147px; width: 988px; height: 554px;
    background: var(--surface); border-radius: 21px;
    box-shadow: 8px 12px 18px rgba(60, 90, 130, 0.35);
  }

  .brand { position: absolute; left: 30px; top: 24px; display: flex; align-items: center; gap: 8px; }
  .brand-dot { width: 14px; height: 14px; border-radius: 50%; background: var(--sky); }
  .brand-name { font-family: "Poppins", sans-serif; font-weight: 500; font-size: 17px; color: var(--ink); }

  .main-nav { position: absolute; top: 28px; left: 0; font-family: "Fira Sans", sans-serif; font-weight: 600; font-size: 11.5px; color: var(--ink); letter-spacing: 0.3px; }
  .main-nav a { position: absolute; white-space: nowrap; color: inherit; text-decoration: none; }
  .main-nav .current::after {
    content: ""; position: absolute; left: -8px; right: -8px; bottom: -7px; height: 2px;
    background: linear-gradient(90deg, var(--coral), var(--sky));
  }

  .hero-title {
    position: absolute; left: 103px; top: 163px; font-weight: 600; font-size: 56px;
    line-height: 54px; letter-spacing: 4px; color: var(--navy); white-space: nowrap;
  }
  .hero-lede {
    position: absolute; left: 103px; top: 305px; font-size: 12.8px; line-height: 23.5px;
    letter-spacing: 0.9px; color: var(--ink); white-space: nowrap;
  }
  .cta { position: absolute; top: 378px; width: 112px; height: 36px; border-radius: 6px;
    font-family: "Fira Sans", sans-serif; font-weight: 500; font-size: 13px; letter-spacing: 0.8px;
    color: #fff; display: flex; align-items: center; justify-content: center; }
  .cta-business { left: 103px; background: var(--coral); }
  .cta-home { left: 224px; background: var(--sky); }

  .price-card {
    position: absolute; left: 525px; top: 149px; width: 349px; height: 301px;
    background: var(--surface); border-radius: 12px;
    box-shadow: 0 4px 16px rgba(30, 37, 83, 0.12);
  }
  .price-chart { position: absolute; left: 0; top: 0; }
  .price { position: absolute; left: 71px; color: var(--navy); }
  .price-value { font-family: "Poppins", sans-serif; font-size: 46px; line-height: 40px; }
  .price-value small { font-size: 23px; }
  .price-unit { font-family: "Fira Sans", sans-serif; font-size: 13.5px; line-height: 16.5px; color: var(--muted); letter-spacing: 0.3px; }
  .price-standard { top: 107px; }
  .price-heating { top: 181px; }

  .compare-card {
    position: absolute; left: 728px; top: 309px; width: 199px; height: 86px;
    background: var(--surface); border-radius: 12px;
    box-shadow: 0 4px 14px rgba(30, 37, 83, 0.14);
  }
  .compare-name { position: absolute; left: 35px; top: 22px; display: flex; align-items: center; gap: 5px;
    font-family: "Fira Sans", sans-serif; font-weight: 600; font-size: 13.5px; color: var(--green); }
  .compare-dot { width: 18px; height: 18px; border-radius: 50%; background: var(--green); }
  .compare-link { position: absolute; left: 34px; top: 49px; font-family: "Fira Sans", sans-serif;
    font-weight: 600; font-size: 11px; letter-spacing: 0.8px; color: var(--navy); white-space: nowrap; }
</style>
</head>
<body>
  <main class="page">
    <div class="brand">
      <span class="brand-dot"></span>
      <span class="brand-name">Vindgerdi</span>
    </div>

    <nav class="main-nav">
      <a class="current" style="left:502px" href="#">Heimasíða</a>
      <a style="left:602px" href="#">Um Vindgerdi</a>
      <a style="left:728px" href="#">Spurt &amp; Svarað</a>
      <a style="left:854px" href="#">Viðskiptaskilmálar</a>
    </nav>

    <h1 class="hero-title">Sama rafmagn<br>Bara ódýrara!</h1>
    <p class="hero-lede">Vindgerdi notar gervigreind, gagnavísindi og sjálfvirkni<br>til að lágmarka kostnað og stuðla að okrujöfnuði</p>

    <a class="cta cta-business">Fyrirtæki</a>
    <a class="cta cta-home">Heimili</a>

    <section class="price-card">
      <svg class="price-chart" width="349" height="140" viewBox="0 0 349 140">
        <path d="M26 57 H66 C90 57 100 94 150 94 C200 94 210 62 240 62 H312" fill="none" stroke="var(--line)" stroke-width="1.5"/>
        <circle cx="75.5" cy="57" r="9.5" fill="#fff" stroke="var(--line)" stroke-width="2"/>
        <circle cx="277.5" cy="62" r="9.5" fill="#fff" stroke="var(--line)" stroke-width="2"/>
        <circle cx="176" cy="94" r="29" fill="#fff" stroke="var(--line)" stroke-width="3"/>
        <circle cx="176" cy="94" r="15.5" fill="var(--alert)"/>
      </svg>
      <div class="price price-standard">
        <div class="price-value">6<small>.98</small></div>
        <div class="price-unit">krónur / kWst</div>
      </div>
      <div class="price price-heating">
        <div class="price-value">6<small>.25</small></div>
        <div class="price-unit">krónur / kWst<br>rafmagnskynding</div>
      </div>
    </section>

    <aside class="compare-card">
      <div class="compare-name"><span class="compare-dot"></span>Verðvaki</div>
      <div class="compare-link">Gerðu verðsamanburð &nbsp;›</div>
    </aside>
  </main>
</body>
</html>
```